Turm7Zwerge
Zielgruppe
Zielgruppe sind die Eltern, Lehrer, Kindergärtner, aber auch Kinder, die bereits Lesen können.
Aufgabenstellung
Ich brauche einen Flyer und ein Plakat für eine Kinderschachschule für Kinder zwischen 4 und 15 Jahren. Auf dem Flyer, den ich in A6-Format drucken möchte (beidseitig), muss ich die Info über die Kinderschachschule Turm7Zwerge (mehr Infos unter www.turm7zwerge-beispiel.ch), dh., was wir machen, Kontaktdaten, etc schreiben können. Es dient als Werbematerial zum Auslegen
Auf dem Plakat wird mehr oder weniger das Gleiche stehen, es wird jedoch als Din A4 Seite aufgehängt.
Unsere Kontaktinformation ist wie folgt:
Turm7Zwerge: Züge für Wolkenkinder
www.turm7zwerge-beispiel.ch

```html
<!DOCTYPE html>
<html lang="de">
<head>
<meta charset="utf-8">
<title>Turm7Zwerge – Kinderschachschule</title>
<link rel="stylesheet" href="https://fonts.googleapis.com/css2?family=Mulish:wght@400;600;700;800&display=swap">
<style>
  :root {
    --cream: #fdf2c4;
    --ink: #1e1e1e;
    --pink: #d8197f;
    --yellow: #efb300;
    --blue: #1f8fd6;
    --band: #2b9ad7;
    --white: #ffffff;
    --placeholder-a: #f5d56a;
    --placeholder-b: #c9c9c9;
  }
  * { margin: 0; padding: 0; box-sizing: border-box; }
  html, body { width: 1200px; height: 1200px; overflow: hidden; background: var(--white); }
  body { font-family: "Mulish", "Century Gothic", sans-serif; color: var(--ink); }
  .flyer { position: relative; width: 1200px; height: 1200px; background: var(--white); }

  .brand-panel {
    position: absolute; left: 0; top: 0; width: 447px; height: 623px;
    background: var(--cream);
  }
  .brand-illustration {
    position: absolute; left: 96px; top: 22px; width: 250px; height: 150px;
    background: linear-gradient(160deg, var(--placeholder-a), var(--placeholder-b));
    border-radius: 6px;
  }
  .brand-name {
    position: absolute; left: 0; top: 196px; width: 447px; text-align: center;
    font-size: 42px; font-weight: 700; color: var(--ink);
  }
  .brand-tagline {
    position: absolute; left: 0; top: 256px; width: 447px; text-align: center;
    font-size: 21px; font-weight: 400; color: var(--ink);
  }
  .benefits { position: absolute; left: 30px; top: 322px; list-style: none; }
  .benefits li {
    display: flex; align-items: center; gap: 14px;
    height: 48.5px; font-size: 22px; font-weight: 700;
  }
  .benefits svg { width: 30px; height: 30px; flex: none; }

  .headline {
    position: absolute; left: 447px; top: 100px; width: 753px; text-align: center;
    font-weight: 800; font-size: 32px; line-height: 72px;
  }
  .c-pink { color: var(--pink); }
  .c-yellow { color: var(--yellow); }
  .c-blue { color: var(--blue); }
  .intro {
    position: absolute; left: 447px; top: 345px; width: 753px; text-align: center;
    font-size: 21px; line-height: 29px;
  }

  .offer-title {
    position: absolute; left: 92px; top: 630px;
    font-size: 27px; font-weight: 600; color: var(--pink);
  }
  .offer-underline { position: absolute; left: 84px; top: 664px; width: 200px; height: 20px; }
  .offer { position: absolute; left: 92px; width: 1060px; font-size: 20.5px; line-height: 28.6px; }
  .offer-local { top: 684px; }
  .offer-region { top: 872px; }
  .offer ul { list-style: none; margin-left: 84px; }
  .offer li { position: relative; padding-left: 24px; }
  .offer li::before {
    content: ""; position: absolute; left: 0; top: 11px;
    width: 8px; height: 8px; border-radius: 50%; background: var(--blue);
  }

  .footer-band {
    position: absolute; left: 0; top: 1058px; width: 1200px; height: 142px;
    background: var(--band); color: var(--white); text-align: center;
    font-size: 22px; line-height: 31px; padding-top: 22px;
  }
  .footer-band .web { color: var(--pink); font-weight: 800; }
</style>
</head>
<body>
<main class="flyer">
  <section class="brand-panel">
    <div class="brand-illustration" role="img" aria-label="Illustration: Schachbrett mit zwei gekrönten Figuren"></div>
    <div class="brand-name">Turm7Zwerge</div>
    <div class="brand-tagline">Züge für Wolkenkinder</div>
    <ul class="benefits">
      <li><svg viewBox="0 0 30 30"><path d="M3 16 L12 25 L27 4" fill="none" stroke="#d8197f" stroke-width="5" stroke-linecap="round" stroke-linejoin="round"/></svg>Konzentrationstraining</li>
      <li><svg viewBox="0 0 30 30"><path d="M3 16 L12 25 L27 4" fill="none" stroke="#d8197f" stroke-width="5" stroke-linecap="round" stroke-linejoin="round"/></svg>Intellektuelle Förderung</li>
      <li><svg viewBox="0 0 30 30"><path d="M3 16 L12 25 L27 4" fill="none" stroke="#d8197f" stroke-width="5" stroke-linecap="round" stroke-linejoin="round"/></svg>Stärkung des Selbstvertrauens</li>
      <li><svg viewBox="0 0 30 30"><path d="M3 16 L12 25 L27 4" fill="none" stroke="#d8197f" stroke-width="5" stroke-linecap="round" stroke-linejoin="round"/></svg>Persönliches Wachstum</li>
      <li><svg viewBox="0 0 30 30"><path d="M3 16 L12 25 L27 4" fill="none" stroke="#d8197f" stroke-width="5" stroke-linecap="round" stroke-linejoin="round"/></svg>Spass und Spannung</li>
    </ul>
  </section>

  <h1 class="headline">Wir bringen Ihr Kind<br>
    <span class="c-pink">Zug</span> <span class="c-yellow">um</span> <span class="c-blue">Zug</span> zum Erfolg!</h1>

  <p class="intro">Wir sind eine Schachschule für Kinder<br>zwischen 4 und15 Jahren.<br>Von Montag bis Samstag bieten wir qualifizierte<br>Schachkurse in Deutsch und Englisch an,<br>welche alter- und niveaumässig<br>auf Ihr Kind zugeschnitten sind.</p>

  <h2 class="offer-title">Wir bieten</h2>
  <svg class="offer-underline" viewBox="0 0 200 20"><path d="M2 14 Q90 4 196 10" fill="none" stroke="#d8197f" stroke-width="3" stroke-linecap="round"/></svg>

  <div class="offer offer-local">
    <p>in unserem eigenem Kurslokal in zentraler Lage in Seefeldheim, Lindenweg 12:</p>
    <ul>
      <li>tägliches Training für alle Alters- und Leistungsstufen<br>von Montag bis Freitag zwischen 13.30 und 19.00 Uhr, sowie Samstags von 10.00-12.00 Uhr</li>
      <li>Auch Vormittags- und Wochenendkurse sind möglich, sowie regelmässige Ferienkurse</li>
      <li>Spätestens ab Januar 2011: mehrere PC-Übungsstationen mit Schachprogrammen,<br>an denen die Schüler kostenlos ihr Wissen vertiefen und testen können.</li>
    </ul>
  </div>

  <div class="offer offer-region">
    <p>im Grossraum Zürich:</p>
    <ul>
      <li>vielfältige private Schachkurse auf Deutsch und Englisch<br>in verschiedenen Alter- und Leistungsstufen.</li>
      <li>Bei Bedarf kommen wir auch in Ihre Nähe.</li>
      <li>Schachkurse und Projekte resp. Schachevents für Schulen und Kindergärten<br>in der gesamten Deutschschweiz</li>
    </ul>
  </div>

  <footer class="footer-band">
    Besuchen Sie uns auch im Internet.<br>
    Weitere ausführliche Informationen erhalten Sie unter<br>
    <span class="web">www.turm7zwerge-beispiel.ch</span>
  </footer>
</main>
</body>
</html>
```